Bridgeway Health of Nations

Please design a business card that is colorful but at the same time easy to read. We are based out on Miami Florida. We are a small start up healthcare company that has been in operation for 1 year. Our clients are Hospitals, Insurance companies, and Manage Care health companies. We are growing quickly and lead the niche we are in. Please make the card 2 sided on the front will be the typical info. Logo, Company Name, Persons Name, Title, Cell #, Office #, Fax#, email, website. No address. On the back we will list 5 services that we do. For example Care Transitions, Case management, Risk assessment, Utilization Review.
Target Market(s)
CEO's and COO's of hospitals and healthcare companies.
Industry/Entity Type
Healthcare

```html
<!DOCTYPE html>
<html lang="en">
<head>
<meta charset="utf-8">
<title>Bridgeway Health of Nations – Business Card</title>
<link href="https://fonts.googleapis.com/css2?family=Arimo:wght@400;700&display=swap" rel="stylesheet">
<style>
  :root {
    --stage: #d9dbde;
    --blue-deep: #1f47b8;
    --blue-mid: #2f6fd6;
    --blue-light: #4aa3ee;
    --band-edge: #2239a6;
    --navy-text: #1b2a6b;
    --rule: #c9d3ea;
    --white: #ffffff;
    --paper: #f4f5f7;
  }
  * { box-sizing: border-box; margin: 0; padding: 0; }
  html, body { width: 1200px; height: 988px; overflow: hidden; }
  body {
    background: var(--stage);
    font-family: "Arimo", Arial, sans-serif;
    display: flex;
    flex-direction: column;
    align-items: center;
    justify-content: center;
    gap: 44px;
  }
  .card {
    width: 760px;
    height: 430px;
    position: relative;
    overflow: hidden;
    box-shadow: 0 8px 24px rgba(0,0,0,0.18);
  }

  /* Shared brand lockup */
  .brand {
    display: flex;
    align-items: center;
    gap: 18px;
  }
  .brand__dot {
    width: 62px; height: 62px;
    border-radius: 50%;
    background: var(--blue-mid);
    flex: none;
  }
  .brand__name {
    font-weight: 700;
    color: var(--navy-text);
    font-size: 30px;
    line-height: 1.05;
  }

  /* Back side */
  .card--back {
    background: radial-gradient(ellipse at center, var(--white) 0%, var(--paper) 100%);
  }
  .band {
    position: absolute;
    left: 0; right: 0;
    height: 78px;
    background: linear-gradient(90deg, var(--band-edge) 0%, var(--blue-mid) 45%, var(--blue-light) 55%, var(--band-edge) 100%);
  }
  .band--top { top: 0; }
  .band--bottom { bottom: 0; }
  .back__body {
    position: absolute;
    top: 78px; bottom: 78px; left: 0; right: 0;
    display: flex;
    align-items: center;
    justify-content: center;
    gap: 40px;
  }
  .back__divider {
    width: 2px;
    height: 170px;
    background: var(--rule);
  }
  .services__title {
    font-size: 14px;
    font-weight: 700;
    letter-spacing: 2px;
    color: var(--blue-mid);
    margin-bottom: 12px;
  }
  .services__list {
    list-style: none;
    display: flex;
    flex-direction: column;
    gap: 9px;
  }
  .service {
    display: flex;
    align-items: center;
    gap: 10px;
    font-size: 17px;
    color: var(--navy-text);
  }
  .service__tick {
    width: 16px; height: 16px;
    flex: none;
  }

  /* Front side */
  .card--front {
    background: radial-gradient(ellipse at 50% 45%, var(--blue-light) 0%, var(--blue-mid) 45%, var(--blue-deep) 100%);
    color: var(--white);
  }
  .front__header {
    position: absolute;
    top: 36px; left: 0; right: 0;
    height: 150px;
    background: var(--white);
    display: flex;
    align-items: center;
    justify-content: center;
  }
  .person {
    position: absolute;
    top: 204px; left: 0; right: 0;
    text-align: center;
  }
  .person__name {
    font-size: 24px;
    letter-spacing: 2px;
  }
  .person__title {
    font-size: 14px;
    letter-spacing: 1.5px;
    margin-top: 4px;
  }
  .contacts {
    position: absolute;
    top: 282px; left: 0; right: 0;
    display: grid;
    grid-template-columns: 230px 290px;
    grid-template-rows: repeat(3, 20px);
    grid-auto-flow: column;
    justify-content: center;
    column-gap: 40px;
    row-gap: 12px;
    font-size: 14px;
  }
  .contact {
    display: flex;
    align-items: center;
    gap: 8px;
    white-space: nowrap;
  }
  .contact__label {
    font-weight: 700;
    width: 46px;
  }
  .contact__icon {
    width: 18px; height: 18px;
    flex: none;
  }
</style>
</head>
<body>

  <section class="card card--back" aria-label="Card back">
    <div class="band band--top"></div>
    <div class="back__body">
      <div class="brand">
        <span class="brand__dot"></span>
        <span class="brand__name">Bridgeway<br>Health of<br>Nations</span>
      </div>
      <div class="back__divider"></div>
      <div class="services">
        <p class="services__title">OUR SERVICES</p>
        <ul class="services__list">
          <li class="service"><svg class="service__tick" viewBox="0 0 16 16" aria-hidden="true"><circle cx="8" cy="8" r="8" fill="#2f6fd6"/><path d="M4.5 8.2l2.3 2.3 4.7-4.9" fill="none" stroke="#fff" stroke-width="1.8"/></svg>Care Transitions</li>
          <li class="service"><svg class="service__tick" viewBox="0 0 16 16" aria-hidden="true"><circle cx="8" cy="8" r="8" fill="#2f6fd6"/><path d="M4.5 8.2l2.3 2.3 4.7-4.9" fill="none" stroke="#fff" stroke-width="1.8"/></svg>Case Management</li>
          <li class="service"><svg class="service__tick" viewBox="0 0 16 16" aria-hidden="true"><circle cx="8" cy="8" r="8" fill="#2f6fd6"/><path d="M4.5 8.2l2.3 2.3 4.7-4.9" fill="none" stroke="#fff" stroke-width="1.8"/></svg>Risk Assessment</li>
          <li class="service"><svg class="service__tick" viewBox="0 0 16 16" aria-hidden="true"><circle cx="8" cy="8" r="8" fill="#2f6fd6"/><path d="M4.5 8.2l2.3 2.3 4.7-4.9" fill="none" stroke="#fff" stroke-width="1.8"/></svg>Utilization Review</li>
          <li class="service"><svg class="service__tick" viewBox="0 0 16 16" aria-hidden="true"><circle cx="8" cy="8" r="8" fill="#2f6fd6"/><path d="M4.5 8.2l2.3 2.3 4.7-4.9" fill="none" stroke="#fff" stroke-width="1.8"/></svg>Discharge Planning</li>
        </ul>
      </div>
    </div>
    <div class="band band--bottom"></div>
  </section>

  <section class="card card--front" aria-label="Card front">
    <div class="front__header">
      <div class="brand">
        <span class="brand__dot"></span>
        <span class="brand__name">Bridgeway<br>Health of<br>Nations</span>
      </div>
    </div>

    <div class="person">
      <p class="person__name">DANIEL REYES</p>
      <p class="person__title">FINANCIAL ADVISOR</p>
    </div>

    <div class="contacts">
      <p class="contact">
        <svg class="contact__icon" viewBox="0 0 18 18" aria-hidden="true">
          <circle cx="9" cy="9" r="9" fill="#fff"/>
          <rect x="6.2" y="3.8" width="5.6" height="10.4" rx="1" fill="none" stroke="#2f6fd6" stroke-width="1.2"/>
          <circle cx="9" cy="12.4" r=".7" fill="#2f6fd6"/>
        </svg>
        <span class="contact__label">Cell</span>305 555 0142
      </p>
      <p class="contact">
        <svg class="contact__icon" viewBox="0 0 18 18" aria-hidden="true">
          <circle cx="9" cy="9" r="9" fill="#fff"/>
          <path d="M6 4.5l1.6 0 .8 2.2-1 .8c.6 1.3 1.6 2.3 2.9 2.9l.8-1 2.2.8v1.6c0 .5-.4.9-.9.9C8.6 12.7 5.3 9.4 5.1 5.4c0-.5.4-.9.9-.9z" fill="#2f6fd6"/>
        </svg>
        <span class="contact__label">Office</span>305 555 0187
      </p>
      <p class="contact">
        <svg class="contact__icon" viewBox="0 0 18 18" aria-hidden="true">
          <circle cx="9" cy="9" r="9" fill="#fff"/>
          <rect x="6" y="4" width="6" height="3.2" fill="none" stroke="#2f6fd6" stroke-width="1.1"/>
          <rect x="4.2" y="7.2" width="9.6" height="4.4" rx=".6" fill="#2f6fd6"/>
          <rect x="6" y="10.6" width="6" height="3.4" fill="#fff" stroke="#2f6fd6" stroke-width="1.1"/>
        </svg>
        <span class="contact__label">Fax</span>305 555 0199
      </p>
      <p class="contact">
        <svg class="contact__icon" viewBox="0 0 18 18" aria-hidden="true">
          <circle cx="9" cy="9" r="9" fill="#fff"/>
          <rect x="4.5" y="6" width="9" height="6.5" fill="none" stroke="#2f6fd6" stroke-width="1.2"/>
          <path d="M4.5 6l4.5 3.6L13.5 6" fill="none" stroke="#2f6fd6" stroke-width="1.2"/>
        </svg>
        d.reyes@bridgewayhealth.com
      </p>
      <p class="contact">
        <svg class="contact__icon" viewBox="0 0 18 18" aria-hidden="true">
          <circle cx="9" cy="9" r="9" fill="#fff"/>
          <circle cx="9" cy="9" r="4.6" fill="none" stroke="#2f6fd6" stroke-width="1.1"/>
          <ellipse cx="9" cy="9" rx="2" ry="4.6" fill="none" stroke="#2f6fd6" stroke-width="1"/>
          <path d="M4.4 9h9.2" stroke="#2f6fd6" stroke-width="1"/>
        </svg>
        www.bridgewayhealth.com
      </p>
    </div>
  </section>

</body>
</html>
```